Card Design for my dog training business Brightpaw Obedience

Need a business card design for my dog training business with my new logo. Want the card to come off professional yet fun. Want it to be very eye catchy as well. I normally have these at vet clinics, pet stores, and groomers. so need it to look better than my competitors.
Target Market(s)
dog owners
Industry/Entity Type
Dog Training
Contact Information for Business Card
needs logo, my name and info
Font styles to use
Serif
Colors
0255a3
ffffff
ec1f27
000000
333333
fbfbfb
Requirements
Must have
- Brightpaw Obedience
- Felix Orland
- 415 903 2276
- info@brightpawobedience.example
- www.brightpawobedience.example

```html
<!DOCTYPE html>
<html lang="en">
<head>
<meta charset="utf-8">
<title>Brightpaw Obedience – Business Card</title>
<link rel="stylesheet" href="https://fonts.googleapis.com/css2?family=EB+Garamond:ital,wght@0,500;1,400&family=Merriweather:wght@400&family=Open+Sans:wght@400&display=swap">
<style>
  :root {
    --stage: #3b3b3d;
    --card-black: #1d1d1f;
    --panel-grey: #3a3d41;
    --silver: #c8c8c8;
    --muted: #9a9a9a;
    --white: #fbfbfb;
    --brand-blue: #0255a3;
    --brand-red: #ec1f27;
  }
  * { margin: 0; padding: 0; box-sizing: border-box; }
  html, body { width: 799px; height: 1200px; overflow: hidden; }
  body { background: var(--stage); position: relative; }

  .card {
    position: absolute;
    left: 60px;
    width: 680px;
    height: 388px;
    background: var(--card-black);
    border-radius: 4px;
    overflow: hidden;
    box-shadow: 0 14px 30px rgba(0,0,0,0.45);
  }
  .card--front { top: 120px; }
  .card--back { top: 690px; }

  .brand-name {
    font-family: "EB Garamond", serif;
    font-weight: 500;
    color: var(--silver);
    text-align: center;
    line-height: 1.05;
    letter-spacing: 1px;
  }
  .card--front .brand-name {
    position: absolute;
    left: 0; right: 0;
    top: 110px;
    font-size: 50px;
  }
  .tagline {
    font-family: "EB Garamond", serif;
    font-style: italic;
    color: var(--muted);
    white-space: nowrap;
  }
  .card--front .tagline {
    position: absolute;
    left: 0; right: 0;
    top: 262px;
    text-align: center;
    font-size: 19px;
  }

  .back-art { position: absolute; inset: 0; }
  .card--back .brand-name {
    position: absolute;
    left: 30px;
    top: 110px;
    width: 230px;
    font-size: 38px;
  }
  .holder {
    position: absolute;
    right: 40px;
    top: 92px;
    text-align: right;
  }
  .holder-name {
    font-family: "Merriweather", serif;
    font-size: 26px;
    color: var(--white);
  }
  .holder-role {
    font-family: "Merriweather", serif;
    font-size: 15px;
    color: var(--silver);
    margin-top: 4px;
  }
  .contact {
    position: absolute;
    right: 36px;
    top: 262px;
    list-style: none;
    font-family: "Open Sans", sans-serif;
    font-size: 15px;
    color: var(--silver);
  }
  .contact li {
    display: flex;
    justify-content: flex-end;
    align-items: center;
    gap: 10px;
    height: 22px;
  }
  .contact svg { width: 14px; height: 14px; fill: var(--brand-blue); flex: none; }
  .card--back .tagline {
    position: absolute;
    right: 60px;
    top: 338px;
    font-size: 16px;
  }
</style>
</head>
<body>

<section class="card card--front">
  <div class="brand-name">Brightpaw<br>Obedience</div>
  <p class="tagline">“Building good habits in every dog, one walk at a time.”</p>
</section>

<section class="card card--back">
  <svg class="back-art" viewBox="0 0 680 388" aria-hidden="true">
    <path d="M175,0 C330,25 400,150 515,205 C585,238 640,244 680,246 L680,0 Z" fill="var(--panel-grey)"/>
    <path d="M120,6 C300,30 385,185 515,238 C585,264 640,262 680,258" fill="none" stroke="var(--brand-blue)" stroke-width="6"/>
    <path d="M110,0 C230,4 315,28 372,72 C320,40 240,18 110,12 Z" fill="var(--brand-red)"/>
  </svg>

  <div class="brand-name">Brightpaw<br>Obedience</div>

  <div class="holder">
    <div class="holder-name">Felix Orland</div>
    <div class="holder-role">Dog Trainer</div>
  </div>

  <ul class="contact">
    <li>415 903 2276
      <svg viewBox="0 0 24 24"><path d="M6.6 10.8a15 15 0 0 0 6.6 6.6l2.2-2.2c.3-.3.7-.4 1-.2 1.1.4 2.300.6 3.6.6.6 0 1 .4 1 1V20c0 .6-.4 1-1 1A17 17 0 0 1 3 4c0-.6.4-1 1-1h3.5c.6 0 1 .4 1 1 0 1.3.2 2.5.6 3.6.1.3 0 .7-.2 1z"/></svg>
    </li>
    <li>info@brightpawobedience.example
      <svg viewBox="0 0 24 24"><path d="M2 5h20v14H2z M3 6l9 7 9-7" fill="var(--brand-blue)" stroke="var(--card-black)" stroke-width="1.5"/></svg>
    </li>
    <li>www.brightpawobedience.example
      <svg viewBox="0 0 24 24"><circle cx="12" cy="12" r="10"/><path d="M2 12h20M12 2c3 3 3 17 0 20M12 2c-3 3-3 17 0 20" fill="none" stroke="var(--card-black)" stroke-width="1.5"/></svg>
    </li>
  </ul>

  <p class="tagline">“Building good habits in every dog, one walk at a time.”</p>
</section>

</body>
</html>
```